Redesign Website - Current one too plain

The description is in the uploaded file. Please let me know if you need any more information. I'd prefer it if someone could implement the design to a WordPress site but the best design will win, regardless.
I would like the forms to look nice as well
UPDATE:
I don't think we can use the images that I provided, I think they make the site look a bit 'cheap' and I really don't know how to replace them. One thought I have had is to make the "Simple, Unique, Effective" a second feature on the right side of the page with the search on the left
Target Market(s)
Small companies, private sellers of cars and people who rent their caravan/holiday home out
Industry/Entity Type
Advertising
Number of Pages Required
3 page
Colors
Designer to choose colors to be used in the design.
Look and feel
Each slider illustrates characteristics of the customer's brand and the style your logo design should communicate.

```html
<!DOCTYPE html>
<html lang="en">
<head>
<meta charset="utf-8">
<title>Plonko – Find advertisers by code</title>
<link rel="stylesheet" href="https://fonts.googleapis.com/css2?family=Poppins:wght@400;600;800&display=swap">
<style>
  :root {
    --ink: #000000;
    --text: #1a1a1a;
    --header-bg: #e0e0df;
    --page-bg: #ececec;
    --page-light: #f7f7f7;
    --panel: #ffffff;
    --rule: #9a9a9a;
    --accent: #e4f21a;
    --photo-light: #f2f2f2;
    --photo-mid: #c9c9c9;
    --photo-dark: #1c1c1c;
  }
  * { box-sizing: border-box; margin: 0; padding: 0; }
  html, body { width: 1200px; height: 782px; overflow: hidden; }
  body {
    position: relative;
    font-family: "Poppins", sans-serif;
    color: var(--text);
    background:
      radial-gradient(ellipse 500px 160px at 300px 110px, var(--page-light), transparent 70%),
      radial-gradient(ellipse 600px 200px at 900px 620px, var(--page-light), transparent 70%),
      linear-gradient(160deg, #eeeeee 0%, #e2e2e2 40%, #f1f1f1 70%, #dedede 100%);
  }

  .site-header {
    position: absolute; left: 0; top: 0; width: 1200px; height: 68px;
    background: var(--header-bg);
  }
  .brand {
    position: absolute; left: 93px; top: 20px;
    display: flex; align-items: center; gap: 8px;
    font-size: 20px; font-weight: 400; letter-spacing: 3px; color: var(--ink);
  }
  .brand-dot { width: 14px; height: 14px; border-radius: 50%; background: var(--ink); }
  .main-nav a {
    position: absolute; top: 30px; font-size: 16px; color: var(--text);
    text-decoration: none; line-height: 1;
  }
  .main-nav .login {
    top: 25px; left: 1025px; width: 86px; height: 32px;
    background: var(--ink); color: var(--accent);
    display: flex; align-items: center; justify-content: center;
  }

  .code-picker { position: absolute; left: 100px; top: 150px; }
  .code-chars {
    position: absolute; left: 0; top: 10px;
    font-size: 120px; font-weight: 800; line-height: 1; color: var(--ink);
    letter-spacing: 2px;
  }
  .chevron { position: absolute; }

  .hero-photo {
    position: absolute; left: 373px; top: 133px; width: 716px; height: 360px;
    border-radius: 120px 90px 40px 40px / 90px 80px 30px 30px;
    background:
      radial-gradient(ellipse 340px 40px at 50% 95%, var(--photo-dark), transparent 80%),
      radial-gradient(ellipse 300px 160px at 55% 40%, var(--photo-light), var(--photo-mid) 80%, transparent 100%);
  }

  .search-bar {
    position: absolute; left: 98px; top: 325px; width: 964px; height: 74px;
    background: var(--panel);
    box-shadow: 0 8px 24px rgba(0,0,0,0.12);
  }
  .search-field {
    position: absolute; top: 26px; height: 22px;
    border-bottom: 1px solid var(--rule);
    font-size: 13px; color: var(--text);
  }
  .search-field .radio {
    position: absolute; right: 2px; top: 5px; width: 10px; height: 10px;
    border: 1px solid #555; border-radius: 50%;
  }
  .search-button {
    position: absolute; left: 779px; top: 22px; width: 118px; height: 32px;
    background: var(--ink); color: var(--accent); border: 0;
    font-family: "Poppins", sans-serif; font-size: 13px;
  }

  .features {
    position: absolute; left: 221px; top: 566px; width: 759px; height: 119px;
    background: var(--panel);
  }
  .feature {
    position: absolute; top: 24px; text-align: center;
  }
  .feature h2 { font-size: 16px; font-weight: 600; color: var(--ink); line-height: 1; }
  .feature p { margin-top: 17px; font-size: 13px; line-height: 18.5px; color: var(--text); }
  .feature-divider {
    position: absolute; top: 22px; width: 1px; height: 75px; background: var(--rule);
  }

  .site-footer {
    position: absolute; left: 0; top: 748px; width: 1200px; height: 34px;
    background: var(--panel); border-top: 1px solid var(--rule);
    text-align: center; font-size: 12.5px; line-height: 34px; color: var(--ink);
  }
</style>
</head>
<body>
  <header class="site-header">
    <div class="brand"><span class="brand-dot"></span>PLONKO</div>
    <nav class="main-nav">
      <a href="#" style="left:599px">Home</a>
      <a href="#" style="left:696px">Advertise</a>
      <a href="#" style="left:819px">Contact</a>
      <a href="#" style="left:932px">Register</a>
      <a href="#" class="login">Login</a>
    </nav>
  </header>

  <div class="hero-photo" role="img" aria-label="White SUV with a small code sticker on its door"></div>

  <section class="code-picker" aria-label="Code selector">
    <svg class="chevron" style="left:31px;top:7px" width="18" height="10" viewBox="0 0 18 10"><path d="M1 9 L9 2 L17 9" fill="none" stroke="#000" stroke-width="2"/></svg>
    <svg class="chevron" style="left:110px;top:7px" width="18" height="10" viewBox="0 0 18 10"><path d="M1 9 L9 2 L17 9" fill="none" stroke="#000" stroke-width="2"/></svg>
    <div class="code-chars">A1</div>
    <svg class="chevron" style="left:31px;top:138px" width="18" height="10" viewBox="0 0 18 10"><path d="M1 1 L9 8 L17 1" fill="none" stroke="#000" stroke-width="2"/></svg>
    <svg class="chevron" style="left:110px;top:138px" width="18" height="10" viewBox="0 0 18 10"><path d="M1 1 L9 8 L17 1" fill="none" stroke="#000" stroke-width="2"/></svg>
  </section>

  <form class="search-bar">
    <label class="search-field" style="left:60px;width:144px">Car<span class="radio"></span></label>
    <label class="search-field" style="left:303px;width:139px">Caravan<span class="radio"></span></label>
    <label class="search-field" style="left:541px;width:140px">Company<span class="radio"></span></label>
    <button type="button" class="search-button">Search</button>
  </form>

  <section class="features">
    <div class="feature" style="left:0;width:225px">
      <h2>Simple</h2>
      <p>create your advert and<br>display your code</p>
    </div>
    <span class="feature-divider" style="left:225px"></span>
    <div class="feature" style="left:226px;width:262px">
      <h2>Unique</h2>
      <p>customers find you by an<br>easy-to-remember code</p>
    </div>
    <span class="feature-divider" style="left:488px"></span>
    <div class="feature" style="left:489px;width:270px">
      <h2>Effective</h2>
      <p>customers are directed to you<br>and not a list of your competitors</p>
    </div>
  </section>

  <footer class="site-footer">© 2023 Plonko. All rights reserved</footer>
</body>
</html>
```